Two Marketing Brochures

We need two professional A4 brochures (PDF + web version) to promote our new handyman services to Facility Managers in Queensland.
Brochure 1: Brightmoor Property Care Trade Services (see content Brightmoor Property Care.pdf). Create new cover page and contents page then design 2 content pages (left and right) I will then paste all text myself, rather than designing 19 pages.
Brochure 2: Brightmoor Property Care Minor Works & Maintenance – Quicker, Tidier, Leaner
Audience: Commercial property managers, Tarrow Gov, councils, schools, industrial clients
Style: Clean, modern, corporate, Brightmoor Property Care-branded
Content: Text is finalised and ready to go
Deliverables: A4 PDF (print-ready) + web version (compressed)
Optional: Integration of JobNest elements (e.g. “Book Now” QR or icon)

```html
<!DOCTYPE html>
<html lang="en">
<head>
<meta charset="utf-8">
<title>Brightmoor Property Care – Trade Services Catalogue</title>
<link rel="stylesheet" href="https://fonts.googleapis.com/css2?family=Cinzel:wght@400;600&family=Open+Sans:wght@400;600;700&display=swap">
<style>
:root{
  --bg:#d6d6d6;
  --navy:#1f3559;
  --navy-deep:#132440;
  --steel:#3e5a84;
  --paper:#ffffff;
  --ink:#27303f;
  --muted:#5b6676;
  --rule:#a9b3c2;
  --band:#e6eaf0;
  --heading:"Cinzel", "Times New Roman", serif;
  --body:"Open Sans", Arial, sans-serif;
}
*{box-sizing:border-box;margin:0;padding:0}
html,body{width:1200px;height:3000px;overflow:hidden;background:var(--bg)}
.canvas{position:relative;width:1200px;height:3000px;background:var(--bg);font-family:var(--body);color:var(--ink)}
.page{position:absolute;width:540px;height:764px;background:var(--paper);overflow:hidden;box-shadow:0 2px 10px rgba(0,0,0,.12)}
.p-cover-a{left:40px;top:150px}
.p-cover-b{left:620px;top:150px}
.p-contents{left:40px;top:1034px}
.p-charge{left:620px;top:1034px}
.p-policy{left:40px;top:1918px}
.p-electrical{left:620px;top:1918px}

/* brand mark */
.brand{display:flex;align-items:center;gap:7px;font-family:var(--heading);font-weight:600;letter-spacing:.5px;white-space:nowrap}
.brand-dot{width:10px;height:10px;border-radius:50%;background:currentColor;flex:none}
.brand--light{color:#fff}
.brand--dark{color:var(--navy)}

/* covers */
.cover-art{position:absolute;inset:0;background:radial-gradient(ellipse at 60% 40%, #3b5580 0%, #24395c 45%, #142540 100%)}
.cover-a-brand{position:absolute;left:34px;top:40px;font-size:14px}
.cover-title{font-family:var(--heading);color:#fff;font-weight:400;line-height:1.12}
.cover-a-title{position:absolute;left:34px;top:320px;font-size:36px}
.cover-sub{font-size:10px;color:#dfe6f0;text-transform:uppercase;line-height:1.4;letter-spacing:.3px}
.cover-a-sub{position:absolute;left:34px;top:418px}
.cover-tag{position:absolute;left:34px;top:640px;width:200px;color:#fff}
.cover-tag h3{font-family:var(--body);font-size:9px;font-weight:700;text-transform:uppercase;line-height:1.35}
.cover-tag p{font-size:7px;line-height:1.45;margin-top:6px;color:#d9e1ec}

.cover-b-center{position:absolute;left:0;right:0;top:300px;text-align:center;display:flex;flex-direction:column;align-items:center}
.cover-b-center .brand{font-size:14px}
.cover-b-title{font-size:32px;margin-top:18px}
.cover-b-sub{margin-top:10px}
.phone-pill{margin-top:16px;display:inline-flex;align-items:center;gap:8px;border:1.5px solid #fff;border-radius:4px;padding:5px 14px;color:#fff;font-size:13px;font-weight:600}

/* light page header */
.page-head{position:absolute;top:22px;right:26px;left:26px;height:30px}
.page-head .rule{position:absolute;left:0;right:190px;top:17px;height:2px;background:var(--navy)}
.page-head .brand{position:absolute;right:0;top:8px;font-size:9.5px}

/* contents */
.contents-title{position:absolute;left:26px;top:62px;font-family:var(--heading);font-size:34px;color:var(--navy);font-weight:400}
.contents-list{position:absolute;left:26px;right:26px;top:118px;list-style:none}
.contents-list li{display:flex;justify-content:space-between;align-items:flex-end;border-bottom:1px solid var(--rule);padding:1px 4px 1px 0}
.contents-list .main{font-size:8.5px;font-weight:700;color:var(--ink);padding-top:6px}
.contents-list .sub{font-size:5.6px;text-transform:uppercase;color:var(--muted);height:12.4px}
.contents-list .sub.cap{text-transform:none}
.contents-list .plain{font-size:6.6px;color:var(--muted);border-bottom:none;height:10px}

/* how we charge */
.charge-title{position:absolute;left:26px;top:60px;font-family:var(--heading);font-size:18px;color:var(--navy);font-weight:600}
.charge-intro{position:absolute;left:26px;top:88px;width:360px;font-size:9.5px;line-height:1.35}
.modes{position:absolute;left:26px;right:28px;top:140px;list-style:none}
.modes::before{content:"";position:absolute;left:12px;top:14px;height:290px;width:1.5px;background:var(--navy)}
.mode{position:relative;padding-left:42px;margin-bottom:34px}
.mode-num{position:absolute;left:0;top:-2px;width:25px;height:25px;border-radius:50%;background:var(--navy);color:#fff;font-size:13px;font-weight:700;display:flex;align-items:center;justify-content:center}
.mode h3{font-family:var(--heading);font-size:11px;color:var(--navy);font-weight:600}
.mode p{font-size:6.8px;line-height:1.5;margin-top:8px}
.charge-photo{position:absolute;left:0;right:0;bottom:0;height:250px;background:linear-gradient(135deg,#c4ccd8 0%,#6f84a6 35%,#1e3457 70%,#0f1d33 100%)}

/* service policy */
.policy-photo{position:absolute;left:0;right:0;top:0;height:228px;background:linear-gradient(160deg,#7b8fae 0%,#3c5479 45%,#1a2c4b 100%)}
.policy-band{position:absolute;left:0;top:228px;width:76px;bottom:0;background:var(--navy)}
.policy-band span{position:absolute;left:50%;bottom:30px;transform-origin:left bottom;transform:translateX(20px) rotate(-90deg);font-family:var(--heading);color:#fff;font-size:38px;white-space:nowrap;letter-spacing:1px}
.policy-body{position:absolute;left:92px;right:22px;top:248px;font-size:5.8px;line-height:1.45}
.policy-block{display:grid;grid-template-columns:1fr 1fr;column-gap:14px;margin-bottom:14px}
.policy-block h3{grid-column:1 / -1;font-size:8.5px;font-weight:700;text-transform:uppercase;color:var(--ink);margin-bottom:4px}
.policy-block h4{font-size:8px;font-weight:600;margin:6px 0 3px}
.policy-block ul{padding-left:9px}
.policy-block li{margin-bottom:2px}
.policy-foot{position:absolute;right:22px;bottom:14px;font-size:8px}

/* electrical overview */
.elec-title{position:absolute;left:26px;top:62px;font-family:var(--heading);font-size:17px;color:var(--navy);font-weight:400}
.service-box{position:absolute;left:22px;right:22px;border:1px solid var(--navy)}
.service-box.one{top:92px}
.service-box.two{top:400px}
.service-box h3{background:var(--navy);color:#fff;font-family:var(--heading);font-size:10px;font-weight:400;text-align:center;padding:5px 0}
.svc-table{display:grid;grid-template-columns:1fr 1fr;font-size:6.2px;line-height:1.45}
.svc-table .th{background:var(--band);font-family:var(--body);font-size:10px;font-weight:600;color:var(--navy);text-align:center;padding:7px 0;border-bottom:1px solid var(--rule)}
.svc-table .td{padding:9px 10px 12px;display:grid;grid-template-columns:1fr 1fr;gap:8px}
.svc-table .td + .td{border-left:1px solid var(--rule)}
.svc-table .th + .th{border-left:1px solid var(--rule)}
.svc-table ul{padding-left:8px}
.svc-table li{margin-bottom:5px}
</style>
</head>
<body>
<main class="canvas">

  <!-- Cover, option A -->
  <section class="page p-cover-a">
    <div class="cover-art" role="img" aria-label="Deep navy hexagon texture background"></div>
    <div class="brand brand--light cover-a-brand"><span class="brand-dot"></span>Brightmoor Property Care</div>
    <h1 class="cover-title cover-a-title">TRADE SERVICES<br>CATALOGUE</h1>
    <p class="cover-sub cover-a-sub">Appliances, Plumbing, Electrical,<br>Heating &amp; Cooling</p>
    <div class="cover-tag">
      <h3>Legendary<br>Service, Delivered Daily</h3>
      <p>BPC is Plumbing, Electrical, Heating, and Cooling on demand. With easy bookings, solid van tracking door-to-door, and clear reports, we're set to get the job done.</p>
    </div>
  </section>

  <!-- Cover, option B -->
  <section class="page p-cover-b">
    <div class="cover-art" role="img" aria-label="Deep navy hexagon texture background"></div>
    <div class="cover-b-center">
      <div class="brand brand--light"><span class="brand-dot"></span>Brightmoor Property Care</div>
      <h1 class="cover-title cover-b-title">TRADE SERVICES<br>CATALOGUE</h1>
      <p class="cover-sub cover-b-sub">Appliances, Plumbing, Electrical,<br>Heating &amp; Cooling</p>
      <div class="phone-pill">
        <svg width="12" height="12" viewBox="0 0 24 24" aria-hidden="true"><path fill="#fff" d="M6.6 10.8a15.1 15.1 0 0 0 6.6 6.6l2.2-2.2c.3-.3.7-.4 1-.2 1.1.4 2.3.6 3.6.6.6 0 1 .4 1 1V20c0 .6-.4 1-1 1A17 17 0 0 1 3 4c0-.6.4-1 1-1h3.5c.6 0 1 .4 1 1 0 1.3.2 2.5.6 3.6.1.3 0 .7-.2 1z"/></svg>
        1300 555 014
      </div>
    </div>
  </section>

  <!-- Table of content -->
  <section class="page p-contents">
    <div class="page-head"><div class="rule"></div><div class="brand brand--dark"><span class="brand-dot"></span>Brightmoor Property Care</div></div>
    <h2 class="contents-title">Table of Content</h2>
    <ol class="contents-list">
      <li class="main"><span>HOW WE CHARGE</span><span>1</span></li>
      <li class="main"><span>SERVICE POLICY</span><span>2</span></li>
      <li class="main"><span>SERVICE OVERVIEW -ELECTRICAL</span><span>3</span></li>
      <li class="sub"><span>Appliance Inspection (Electrical,Gas,Water)</span><span>3</span></li>
      <li class="sub"><span>Electrical Safety Inspection</span><span>3</span></li>
      <li class="sub"><span>Smoke Alarm Compliance Inspection</span><span>3</span></li>
      <li class="sub"><span>Thermal Imaging - Switchboards</span><span>3</span></li>
      <li class="sub"><span>Light Switch Replacement</span><span>4</span></li>
      <li class="sub"><span>Powerpoint Replacement</span><span>4</span></li>
      <li class="sub"><span>Ceiling Exhaust Fan Replacement</span><span>4</span></li>
      <li class="sub"><span>Down Light Replacement</span><span>4</span></li>
      <li class="main"><span>SERVICE OVERVIEW PLUMBING</span><span>5</span></li>
      <li class="sub"><span>Gas Safety Inspection</span><span>5</span></li>
      <li class="sub"><span>Flexi Hose Inspection</span><span>5</span></li>
      <li class="sub"><span>Hot Water Faults</span><span>5</span></li>
      <li class="sub"><span>Temporary Hot Water Installation</span><span>6</span></li>
      <li class="sub cap"><span>MAJOR BLOCKAGE (Storm and Sewer)</span><span>6</span></li>
      <li class="sub"><span>Roof Leak and Assessment</span><span>6</span></li>
      <li class="sub cap"><span>LEAK DETECTION - Minor Waste Blockages (Sink, Basin, Shower, etc.)</span><span>6</span></li>
      <li class="main"><span>SERVICE OVERVIEW - HEATING &amp; COOLING</span><span>7</span></li>
      <li class="sub"><span>AC Split System Inspection &amp; Diagnosis</span><span>7</span></li>
      <li class="sub"><span>AC Split System Service/Inspection</span><span>7</span></li>
      <li class="sub"><span>AC Split System Hydro Clean</span><span>8</span></li>
      <li class="sub"><span>Gas Ducted Heating Service/Inspection</span><span>8</span></li>
      <li class="sub"><span>Temporary Heating/Cooling</span><span>8</span></li>
      <li class="sub cap"><span>LEAK DETECTION - Minor Waste Blockages (Sink, Basin, Shower, etc.)</span><span>8</span></li>
      <li class="main"><span>SERVICE OVERVIEW - HEATING &amp; COOLING</span><span>9</span></li>
      <li class="main"><span>SERVICE CHARGES</span><span>10</span></li>
      <li class="plain"><span>Electrical</span><span>10</span></li>
      <li class="plain"><span>Heating &amp; Cooling</span><span>10</span></li>
      <li class="plain"><span>Plumbing</span><span>10</span></li>
      <li class="plain"><span>Appliances</span><span>10</span></li>
    </ol>
  </section>

  <!-- How we charge -->
  <section class="page p-charge">
    <div class="page-head"><div class="rule"></div><div class="brand brand--dark"><span class="brand-dot"></span>Brightmoor Property Care</div></div>
    <h2 class="charge-title">HOW WE CHARGE</h2>
    <p class="charge-intro">We have simplified charging to 3 different modes - so you always have control over your costs</p>
    <ol class="modes">
      <li class="mode"><span class="mode-num">1</span>
        <h3>Mode :Do and Charge</h3>
        <p>This is when nobody is sure what a problem is and what needs to be done. Think of it as a general service, where we send a plumber, electrician, or heating &amp; cooling specialist to site and attempt to make repairs, whatever they are.</p>
      </li>
      <li class="mode"><span class="mode-num">2</span>
        <h3>Mode :Flat Rate Service</h3>
        <p>In the following pages, we have listed our standard services with a fixed price. This way, you will know exactly what you will pay for these services, and they are exactly as described. If there is any variation or addition to these costs, we will not proceed without authorised approval.</p>
      </li>
      <li class="mode"><span class="mode-num">3</span>
        <h3>Mode :Quote</h3>
        <p>Where a job can be clearly scoped, and no additional technical information is required, we will provide a free quote for your consideration. We will attend the site and take required measurements. If a fault finding or technical assessment is required on-site before a quote is submitted, then we will need to attend as a 'do and charge'.</p>
      </li>
    </ol>
    <div class="charge-photo" role="img" aria-label="Photo of a person selecting a rating on a laptop screen"></div>
  </section>

  <!-- Service policy -->
  <section class="page p-policy">
    <div class="policy-photo" role="img" aria-label="Photo of a team joining hands over a table with connected service icons"></div>
    <div class="policy-band"><span>SERVICE POLICY</span></div>
    <div class="policy-body">
      <div class="policy-block">
        <h3>Normal Hours Service</h3>
        <ul>
          <li>Service call includes first 15 minutes of labour.</li>
          <li>Labour is then charged per 15 minute block thereafter.</li>
          <li>Complies only requested or approved works.</li>
          <li>Photos, before and after.</li>
        </ul>
        <ul>
          <li>All required material, sundries and consumables will be charged as additional.</li>
          <li>Removal and disposal of all rubbish related to works.</li>
          <li>Area cleaned upon completion of work.</li>
        </ul>
        <div>
          <h4>Works Do Not Include</h4>
          <ul><li>Moving of any heavy/bulky furniture to access works.</li></ul>
          <h4>Important Notes</h4>
          <ul>
            <li>If further works are required beyond the initial scope, a quote will be issued and approved before any work proceeds.</li>
            <li>Parts ordered will be fitted on a return visit at the agreed rate.</li>
          </ul>
        </div>
        <div>
          <ul>
            <li>Any major remedial works/repairs or replacements will not proceed without prior written approval.</li>
            <li>After 5 days of no action on further approval, we will close the job and a new work order will be needed.</li>
          </ul>
        </div>
      </div>
      <div class="policy-block">
        <h3>After Hours Service</h3>
        <ul>
          <li>Service does not include any labour.</li>
          <li>Minimum charge of 1 hour labour.</li>
          <li>After hours loading includes total trip travel up to 30km.</li>
          <li>Labour is charged per 15 minute block after the first hour.</li>
        </ul>
        <ul>
          <li>Quality over the phone if the job is 'urgent' for the Residential Tenancies Act.</li>
          <li>Complete minimum works to make the site safe and habitable.</li>
          <li>Complete minor repairs/replacements to avoid inconvenience.</li>
        </ul>
        <div>
          <h4>Works Do Not Include</h4>
          <ul><li>Moving of any heavy/bulky furniture to access works when reasonably able to do so.</li></ul>
          <h4>Important Notes</h4>
          <ul>
            <li>Works will only be attempted where the area is deemed safe.</li>
            <li>Where temporary services are installed, further works will be quoted and approved in normal hours.</li>
          </ul>
        </div>
        <div>
          <ul>
            <li>Any major remedial works/repairs or replacements.</li>
            <li>Any removal of trade waste from site.</li>
            <li>Works where excessive noise will be generated after hours may be rescheduled to a suitable time.</li>
          </ul>
        </div>
      </div>
    </div>
    <div class="brand brand--dark policy-foot"><span class="brand-dot"></span>Brightmoor Property Care</div>
  </section>

  <!-- Service overview electrical -->
  <section class="page p-electrical">
    <div class="page-head"><div class="rule"></div><div class="brand brand--dark"><span class="brand-dot"></span>Brightmoor Property Care</div></div>
    <h2 class="elec-title">SERVICE OVERVIEW - ELECTRICAL</h2>

    <div class="service-box one">
      <h3>APPLIANCE INSPECTION (ELECTRICAL, GAS, WATER)</h3>
      <div class="svc-table">
        <div class="th">Works Include</div>
        <div class="th">Important Notes</div>
        <div class="td">
          <ul>
            <li>Testing and diagnosis of appliance issue.</li>
            <li>Report detailing the appliance issue or repairs made.</li>
            <li>Quotation for replacement of appliance if beyond reasonable and practical repair.</li>
          </ul>
          <ul>
            <li>Photos: before and after.</li>
            <li>Removal and disposal of all rubbish related to works.</li>
            <li>Area cleaned upon completion of work.</li>
            <li>Minor repairs where economical to do so.</li>
          </ul>
        </div>
        <div class="td">
          <ul>
            <li>To test and work on appliances, all appliances must be readily accessible. If we must wait an extended time for an appliance to become accessible, additional hourly charges will be incurred.</li>
          </ul>
          <ul>
            <li>All appliances/equipment must be reasonably accessible and in a clean environment. Technicians cannot move dirty dishes or laundry to access an appliance.</li>
            <li>No responsibility is taken for goods damaged while working.</li>
          </ul>
        </div>
      </div>
    </div>

    <div class="service-box two">
      <h3>ELECTRICAL SAFETY INSPECTION</h3>
      <div class="svc-table">
        <div class="th">Works Include</div>
        <div class="th">Important Notes</div>
        <div class="td">
          <ul>
            <li>Testing of all accessible parts of the electrical installation, including visual inspection.</li>
            <li>Mandatory testing in accordance with AS/NZS 3019:2022</li>
          </ul>
          <ul>
            <li>Photos: before and after.</li>
            <li>Removal and disposal of all rubbish related to works.</li>
            <li>Audit report showing compliance and/or defect list.</li>
            <li>Area cleaned upon completion of work.</li>
          </ul>
        </div>
        <div class="td">
          <ul>
            <li>If any part of the electrical installation is found to present clear and immediate danger to property or persons, then we will disconnect that appliance or part of the installation from supply and quote for remedial works later.</li>
            <li>Power must be connected to the property.</li>
          </ul>
          <ul>
            <li>All parts of the installation and equipment must be reasonably accessible and in a clean environment. Technicians cannot crawl under furniture to access light fixtures, power outlets or smoke alarms.</li>
          </ul>
        </div>
      </div>
    </div>
  </section>

</main>
</body>
</html>
```